Small Business Broker Business Card Design

A business card design for a small business brokerage, which is a financial service, not unlike real estate brokerage, but for small businesses such as laundromats, pizza shops, restaurants, cleaners etc. The designs should all be simple, more conservative in nature, using the colors and font of the logo. Again, think real estate Brokerage as a business context
Contact Information for Business Card
Name: Glen R. Harlow. Title: Small Business Advisor. Email: g.harlow@bayfieldcapitalworks.example. Mobile: (555) 274-3918. Office: (555) 806-2147. www.bayfieldcapitalworks.example

```html
<!DOCTYPE html>
<html lang="en">
<head>
<meta charset="utf-8">
<title>Bayfield Capital Works — Business Card</title>
<link href="https://fonts.googleapis.com/css2?family=Montserrat:wght@600;700&family=Arimo:wght@400;700&display=swap" rel="stylesheet">
<style>
  :root{
    --stage:#1b1b1d;
    --navy:#15305f;
    --green:#7dc242;
    --white:#ffffff;
    --paper:#f8f8f4;
    --rule:#c9d3e3;
  }
  *{box-sizing:border-box;margin:0;padding:0}
  html,body{width:1200px;height:963px;overflow:hidden;background:var(--stage)}
  .stage{width:1200px;height:963px;display:flex;flex-direction:column;align-items:center;justify-content:center;gap:40px}
  .card{width:700px;height:400px;border-radius:28px;position:relative;overflow:hidden}
  .card--front{background:var(--navy);color:var(--white)}
  .card--back{background:var(--paper);display:flex;flex-direction:column;justify-content:center;padding-left:70px}

  .brand{position:absolute;top:92px;left:230px;display:flex;align-items:center;gap:16px}
  .brand__square{width:34px;height:34px;background:var(--green)}
  .brand__name{font-family:"Montserrat",sans-serif;font-weight:700;font-size:22px;letter-spacing:1.5px;text-transform:uppercase;color:var(--white)}
  .brand__tagline{position:absolute;top:136px;left:280px;font-family:"Montserrat",sans-serif;font-weight:600;font-size:10.5px;letter-spacing:1.6px;text-transform:uppercase;color:var(--green)}

  .person{position:absolute;left:60px;top:250px;text-align:right;width:250px}
  .person__name{font-family:"Montserrat",sans-serif;font-weight:700;font-size:25px;letter-spacing:1px;text-transform:uppercase}
  .person__title{font-family:"Arimo",sans-serif;font-size:16px;color:var(--green);margin-top:4px}
  .divider{position:absolute;left:330px;top:238px;width:1px;height:100px;background:var(--rule)}
  .contact{position:absolute;left:350px;top:240px;font-family:"Arimo",sans-serif;font-size:14.5px;line-height:24px;list-style:none}
  .contact__label{color:var(--green);font-weight:700;margin-right:4px}

  .back__name{font-family:"Montserrat",sans-serif;font-weight:700;font-size:32px;letter-spacing:2px;text-transform:uppercase;color:var(--navy)}
  .back__tagline{font-family:"Montserrat",sans-serif;font-weight:600;font-size:14px;letter-spacing:2.4px;text-transform:uppercase;color:var(--green);margin-top:6px}
</style>
</head>
<body>
<main class="stage">
  <section class="card card--front" aria-label="Card front">
    <div class="brand">
      <span class="brand__square"></span>
      <span class="brand__name">Bayfield Capital Works, Inc</span>
    </div>
    <p class="brand__tagline">Confidently buy or sell a local business today</p>

    <div class="person">
      <h1 class="person__name">Glen R. Harlow</h1>
      <p class="person__title">Small Business Advisor</p>
    </div>
    <span class="divider"></span>
    <ul class="contact">
      <li><span class="contact__label">O:</span>(555) 806-2147</li>
      <li><span class="contact__label">M:</span>(555) 274-3918</li>
      <li><span class="contact__label">E:</span>g.harlow@bayfieldcapitalworks.example</li>
      <li>www.bayfieldcapitalworks.example</li>
    </ul>
  </section>

  <section class="card card--back" aria-label="Card back">
    <h2 class="back__name">Bayfield Capital Works, Inc</h2>
    <p class="back__tagline">Confidently buy or sell a local business today</p>
  </section>
</main>
</body>
</html>
```